Harrow Point Metrics Company Website Design and Coding

We want to redesign our existing website so that it is more visually and functionally appealing to prospective clients and potential job candidates. We would like to keep our current color scheme and implement our current logo as well. We have a high-level idea of website structure that we are thinking of, which is in the attached files. Logo is included as well. The final design would ideally be energy and analytics focused. We will need the new website to be coded as well, please.

Target Market(s)

Energy and utility industry

Industry/Entity Type

Energy/analytics

Coding

Coded - Design and coding required

Number of Pages Required

5+ page

Font styles to use
Sans Serif

Colors
0094D4
00A9DD
6FCCEA
C7EBF8
E9F6FB
F0912C
F2A743
F7CA91
FBE8D2
FDF5EE

Requirements
Must have
• Consistent color scheme- please use the one that we provided. We need an overview, a home page, and our core services. A separate job application page. Logo must be incorporated. We would like e "Meet our Team" page. Please include all of the content that is listed in our attachments.
Nice to have
• Movement
Should not have
• No music, no cartoons/animation, no pictures of a chalkboard

```html
<!DOCTYPE html>
<html lang="en">
<head>
<meta charset="utf-8">
<title>Harrow Point Metrics</title>
<link href="https://fonts.googleapis.com/css2?family=Rajdhani:wght@400;500;600;700&family=Arimo:wght@400&display=swap" rel="stylesheet">
<style>
:root{
  --blue:#0094D4;
  --blue-2:#00A9DD;
  --blue-3:#6FCCEA;
  --blue-4:#C7EBF8;
  --blue-5:#E9F6FB;
  --orange:#F0912C;
  --orange-2:#F2A743;
  --orange-3:#F7CA91;
  --ink:#4a4a4a;
  --body:#6b6b6b;
  --dark:#232325;
  --head:'Rajdhani',sans-serif;
  --sans:'Arimo',Arial,sans-serif;
}
*{box-sizing:border-box;margin:0;padding:0}
html,body{width:1200px;height:4298px;overflow:hidden}
body{font-family:var(--head);color:var(--ink);background:#fff;position:relative}
.abs{position:absolute}
.brand{font-family:var(--head);font-weight:500;color:var(--blue);display:flex;align-items:center;gap:10px}
.brand .dot{width:30px;height:30px;border-radius:50%;background:var(--blue-4)}
.brand small{display:block;font-size:10px;letter-spacing:2px;color:#8a8a8a;font-weight:500}

/* header */
.site-header{top:0;left:0;width:1200px;height:120px;background:#fff;border-bottom:1px solid #eee}
.site-header .brand{position:absolute;left:112px;top:34px;font-size:22px;line-height:1}
.main-nav{position:absolute;left:420px;top:0;height:120px;display:flex;align-items:center;gap:32px;font-size:15px;font-weight:600;color:#3a3a3a}
.main-nav .active{color:var(--blue-2)}
.btn-start{position:absolute;left:961px;top:43px;width:127px;height:45px;background:var(--orange);color:#fff;font-size:14px;font-weight:600;display:flex;align-items:center;justify-content:center;border-radius:2px}

/* hero */
.hero{top:120px;left:0;width:1200px;height:705px;background:linear-gradient(120deg,#0a1236 0%,#1b3aa8 40%,#0d1d5c 70%,#0a0f2a 100%)}
.hero-title{left:112px;top:307px;height:69px;width:509px;background:var(--blue);color:#fff;font-size:47px;font-weight:600;padding-left:22px;line-height:69px}
.hero-sub{left:112px;top:386px;height:68px;width:611px;background:var(--orange);color:#fff;font-size:40px;font-weight:600;padding-left:22px;line-height:68px}
.hero-dots{left:576px;top:682px;display:flex;gap:6px}
.hero-dots span{width:11px;height:11px;border-radius:50%;background:#fff}
.hero-dots span.on{background:var(--orange)}

/* welcome */
.welcome-kicker{left:112px;top:912px;font-size:32px;font-weight:500;color:#555}
.welcome-title{left:112px;top:955px;font-size:40px;font-weight:600;color:var(--blue)}
.welcome-text{left:112px;top:1022px;width:500px;font-size:15.5px;line-height:28.5px;color:var(--body);text-align:justify}
.btn-blue{background:var(--blue);color:#fff;font-weight:700;font-size:16px;display:flex;align-items:center;justify-content:center;border-radius:2px}
.welcome-btn{left:112px;top:1222px;width:150px;height:52px}
.welcome-art{left:700px;top:926px;width:318px;height:392px;border-radius:50% 40% 50% 30%;background:radial-gradient(circle at 40% 35%,var(--blue-4),#fff 70%)}

/* services */
.services{top:1365px;left:0;width:1200px;height:638px;background:#f2f9fd}
.section-title{width:1200px;left:0;text-align:center;font-size:42px;font-weight:500;color:#444}
.section-title b{color:var(--blue);font-weight:600}
.section-title::after{content:"";display:block;width:44px;height:3px;background:var(--blue);margin:6px auto 0}
.service-card{top:1490px;width:228px;height:443px;color:#fff;text-align:center}
.service-card.blue{background:var(--blue)}
.service-card.orange{background:var(--orange)}
.service-card .thumb{height:212px}
.service-card h3{font-size:18px;font-weight:600;line-height:26px;margin:20px 10px 6px;min-height:52px;display:flex;align-items:center;justify-content:center}
.service-card p{font-size:13.5px;line-height:25px;margin:0 14px}
.service-card .more{display:inline-block;margin-top:14px;border:1px solid #fff;width:117px;height:40px;line-height:38px;font-size:15px;font-weight:500}
.slider-arrow{top:1680px;width:52px;height:52px;border-radius:50%;border:1px solid #bbb;background:#fff;display:flex;align-items:center;justify-content:center}

/* research */
.research-img{width:487px;height:305px}
.research h3{font-size:26px;font-weight:600;color:var(--blue);line-height:35px}
.research p{font-size:15.5px;line-height:27.5px;color:var(--body);margin-top:14px}
.btn-outline{display:inline-flex;align-items:center;justify-content:center;border:2px solid var(--blue);color:var(--blue);width:132px;height:50px;font-weight:700;font-size:16px;margin-top:18px}

/* teams */
.team-card{top:3021px;width:312px;height:309px;border:3px solid var(--blue-2);border-radius:4px;text-align:center;background:#fff}
.team-card .avatar{position:absolute;left:83px;top:-56px;width:146px;height:146px;border-radius:50%;background:linear-gradient(160deg,#d8d8d8,#8d8d8d);border:4px solid #fff}
.team-card h4{margin-top:108px;font-size:20px;font-weight:500;color:var(--blue)}
.team-card .role{font-family:var(--sans);font-size:14px;color:#555;margin-top:4px}
.team-card .bio{font-family:var(--sans);font-size:13.5px;line-height:26px;color:#444;margin:6px 24px 0}
.team-card .in{position:absolute;left:136px;top:241px;width:40px;height:40px;border-radius:50%;background:var(--blue-2);color:#fff;font-size:15px;font-weight:700;line-height:40px}

/* about */
.about{top:3397px;left:0;width:1200px;height:517px;background:linear-gradient(90deg,#cfd6dc 0%,#eef1f3 45%,#f8f9fa 60%,#fff 100%)}
.about-title{left:698px;top:3457px;font-size:42px;font-weight:600;color:#444}
.about-text{left:700px;top:3537px;width:335px;font-size:15.5px;line-height:24.2px;color:var(--body);text-align:justify}
.btn-orange{left:701px;top:3795px;width:145px;height:51px;background:var(--orange);color:#fff;font-weight:700;font-size:16px;display:flex;align-items:center;justify-content:center}

/* footer */
.site-footer{top:3914px;left:0;width:1200px;height:384px;background:var(--dark);color:#fff}
.site-footer .brand{position:absolute;left:418px;top:50px;font-size:30px;color:var(--blue-2)}
.site-footer .brand small{color:#bbb;font-size:11px;letter-spacing:3px}
.footer-nav{position:absolute;left:0;width:1200px;top:147px;display:flex;justify-content:center;gap:46px;font-size:15px;font-weight:600}
.footer-contact{position:absolute;top:195px;left:112px;width:976px;border-top:1px solid #3c3c3e;border-bottom:1px solid #3c3c3e;height:110px;display:flex;align-items:center;justify-content:space-between;font-size:14px;font-family:var(--head);font-weight:500}
.footer-contact .item{display:flex;align-items:center;gap:16px}
.footer-contact .ic{width:44px;height:44px;border-radius:50%;border:1px solid #ddd;display:flex;align-items:center;justify-content:center}
.socials{position:absolute;left:112px;top:325px;display:flex;gap:8px}
.socials span{width:40px;height:40px;border-radius:50%;border:1.5px solid #fff}
.copy{position:absolute;right:112px;top:337px;font-size:14px;font-weight:500}
</style>
</head>
<body>

<header class="site-header abs">
  <div class="brand"><span class="dot"></span><div>Harrow Point Metrics<small>DATA DRIVEN RESEARCH AND INSIGHTS</small></div></div>
  <nav class="main-nav">
    <span class="active">Home</span><span>Core Services</span><span>About Us</span><span>Our Work</span><span>Blog</span><span>Contact Us</span>
  </nav>
  <div class="btn-start">GET STARTED</div>
</header>

<section class="hero abs" role="img" aria-label="Photo of a hand using a stylus on a tablet showing analytics charts, with glowing numbers"></section>
<div class="hero-title abs">Harrow Point Metrics</div>
<div class="hero-sub abs">Data Driven Research &amp; Insights</div>
<div class="hero-dots abs"><span></span><span class="on"></span><span></span></div>

<div class="welcome-kicker abs">Welcome To</div>
<h1 class="welcome-title abs">Harrow Point Metrics</h1>
<p class="welcome-text abs">Harrow Point Metrics was formed in 2016 to help utilities and regulatory agencies navigate the technical, economic, and policy challenges of building a smarter and cleaner energy future. Through cutting edge research design and analysis methods we provide DSM program administrators with data-driven insights into how various technologies and interventions affect the way homes and businesses use energy.</p>
<div class="welcome-btn btn-blue abs">READ MORE</div>
<div class="welcome-art abs" role="img" aria-label="Curved grid of blue dots forming a flowing data surface"></div>

<section class="services abs"></section>
<h2 class="section-title abs" style="top:1395px">Our <b>Services</b></h2>
<div class="slider-arrow abs" style="left:41px"><svg width="14" height="14" viewBox="0 0 14 14"><path d="M9 2 4 7l5 5" fill="none" stroke="#444" stroke-width="1.6"/></svg></div>
<div class="slider-arrow abs" style="left:1107px"><svg width="14" height="14" viewBox="0 0 14 14"><path d="M5 2l5 5-5 5" fill="none" stroke="#444" stroke-width="1.6"/></svg></div>

<article class="service-card blue abs" style="left:112px">
  <div class="thumb" role="img" aria-label="Laptop keyboard with floating data icons" style="background:linear-gradient(160deg,#0c4f8a,#4fb4e6)"></div>
  <h3>Predictive Analytics<br>and Forecasting</h3>
  <p>Distributed energy resource integration into planning and operations</p>
  <span class="more">Read More</span>
</article>
<article class="service-card orange abs" style="left:361px">
  <div class="thumb" role="img" aria-label="Laptop with holographic charts" style="background:linear-gradient(160deg,#0f1a33,#3b79b8)"></div>
  <h3>T&amp;D Planning</h3>
  <p>Location specific, probabilistic forecasting for system trans mission &amp; distribution planning</p>
  <span class="more">Read More</span>
</article>
<article class="service-card blue abs" style="left:611px">
  <div class="thumb" role="img" aria-label="City skyline at night with rising light graph" style="background:linear-gradient(180deg,#0d1630,#2a4a80)"></div>
  <h3>Pilot &amp; Emerging<br>Tech Support</h3>
  <p>Design and implementation of pilots and controlled deployments</p>
  <span class="more">Read More</span>
</article>
<article class="service-card orange abs" style="left:860px">
  <div class="thumb" role="img" aria-label="Robot hand touching a tablet beside a laptop" style="background:linear-gradient(160deg,#d5e6f2,#2a7fc2)"></div>
  <h3>Program Portfolio &amp;<br>Resource Planning</h3>
  <p>End-use/load profile studies &amp; research End-use saturation and baseline studies</p>
  <span class="more">Read More</span>
</article>

<h2 class="section-title abs" style="top:2038px">Research <b>&amp; Analysis</b></h2>
<div class="research-img abs" style="left:112px;top:2140px;background:linear-gradient(150deg,#0b1a2c,#5a3a24 55%,#0e2036)" role="img" aria-label="Aerial night view of city streets with light trails"></div>
<div class="research abs" style="left:651px;top:2155px;width:420px">
  <h3>Journal Articles and Conference Presentations</h3>
  <p>Sed ut perspiciatis unde omnis iste natus error sit voluptatem accusantium doloremque laudantium, totam rem aperiam, eaq ue ipsa quae ab illo inventore veritatis et quasi architecto beat ae vitae dicta sunt explicabo.</p>
  <span class="btn-outline">READ MORE</span>
</div>
<div class="research abs" style="left:145px;top:2505px;width:420px">
  <h3>Published Reports</h3>
  <p>Sed ut perspiciatis unde omnis iste natus error sit voluptatem accusantium doloremque laudantium, totam rem aperiam, eaq ue ipsa quae ab illo inventore veritatis et quasi architecto beat ae vitae dicta sunt explicabo.</p>
  <span class="btn-outline">READ MORE</span>
</div>
<div class="research-img abs" style="left:601px;top:2447px;background:linear-gradient(150deg,#0a1f3e,#1c6aa8 50%,#0b2a2a)" role="img" aria-label="Hand pointing a pen at a financial chart on a screen"></div>

<div class="abs" style="left:0;top:2829px;width:1200px;height:1px;background:#eee"></div>
<h2 class="section-title abs" style="top:2857px">Our <b>Teams</b></h2>
<article class="team-card abs" style="left:112px">
  <div class="avatar" role="img" aria-label="Portrait of Owen Kessler"></div>
  <h4>Owen Kessler, M.S</h4>
  <div class="role">Partner</div>
  <p class="bio">Owen Kessler is an applied statistician whose work is centered around estimat ing the impacts of demand</p>
  <span class="in">in</span>
</article>
<article class="team-card abs" style="left:444px">
  <div class="avatar" role="img" aria-label="Portrait of Ravi Mendel"></div>
  <h4>Ravi Mendel, M.P.P.</h4>
  <div class="role">Partner</div>
  <p class="bio">Ravi Mendel specializes in advanced applications of data analytics using large volu mes of hourly and sub-hourly</p>
  <span class="in">in</span>
</article>
<article class="team-card abs" style="left:776px">
  <div class="avatar" role="img" aria-label="Portrait of Clara Dunmore"></div>
  <h4>Clara Dunmore</h4>
  <div class="role">Partner</div>
  <p class="bio">Ms. Dunmore's work has focused an array of Distributed Energy Resources (DERs) from solar photo</p>
  <span class="in">in</span>
</article>

<section class="about abs"></section>
<div class="abs" style="left:0;top:3397px;width:640px;height:517px;background:linear-gradient(120deg,#aab4bc,#e6ebee 60%,rgba(255,255,255,0))" role="img" aria-label="Desk with desktop monitor, laptop, tablet and mug showing dashboards"></div>
<h2 class="about-title abs">About Us</h2>
<p class="about-text abs">Harrow Point Metrics (HPM) was formed in 2016 to help utilities and regulatory agencies navigate the technical, economic, and policy challenges of building a smarter and cleaner energy future. Our research focuses on impact analysis as well as predictive &amp; causal analytics. We deliver data-driven insights into how various technologies and interventions affect the way homes and businesses use energy and how those in turn affect grid and system planning.</p>
<div class="btn-orange abs">READ MORE</div>

<footer class="site-footer abs">
  <div class="brand"><span class="dot"></span><div>Harrow Point Metrics<small>DATA DRIVEN RESEARCH AND INSIGHTS</small></div></div>
  <nav class="footer-nav"><span>HOME</span><span>CORE SERVICES</span><span>ABOUT US</span><span>OUR WORK</span><span>BLOG</span><span>CONTACT US</span></nav>
  <div class="footer-contact">
    <div class="item" style="margin-left:40px"><span class="ic"><svg width="16" height="20" viewBox="0 0 16 20"><path d="M8 1a6 6 0 0 0-6 6c0 5 6 12 6 12s6-7 6-12a6 6 0 0 0-6-6z" fill="#fff"/><circle cx="8" cy="7" r="2.2" fill="#232325"/></svg></span><span>48 Larkfield Row<br>Suite B2 Denver, CO 80205</span></div>
    <div class="item"><span class="ic"><svg width="18" height="18" viewBox="0 0 18 18"><path d="M4 1l3 4-2 2c1 2 3 4 5 5l2-2 4 3-2 3C7 16 2 11 1 4z" fill="#fff"/></svg></span><span>555.014.2276</span></div>
    <div class="item" style="margin-right:10px"><span class="ic"><svg width="18" height="14" viewBox="0 0 18 14"><rect x="1" y="1" width="16" height="12" rx="1" fill="#fff"/><path d="M1 2l8 6 8-6" fill="none" stroke="#232325" stroke-width="1.4"/></svg></span><span>info@harrowpointmetrics.com</span></div>
  </div>
  <div class="socials"><span></span><span></span><span></span></div>
  <div class="copy">© 2022 Harrow Point Metrics.All rights reserved</div>
</footer>

</body>
</html>
```